Redesign of Medical App for Patients

• The Designer’s task is to provide a new fully-responsive design for our apps, and then code it using only basic html and CSS.
• Your design will be incorporated into our existing REACT native app.

Target Market(s)

Medical Patients

Industry/Entity Type

Medical

Coding

Coded - Design and coding required

Number of Pages Required

5+ page

Requirements
Must have
• Short list candidates will receive detailed briefing
Nice to have
• detailed briefing contains some of our ideas.

```html
<!DOCTYPE html>
<html lang="en">
<head>
<meta charset="utf-8">
<title>CarePath – Patient App Screens</title>
<link rel="stylesheet" href="https://fonts.googleapis.com/css2?family=Montserrat:wght@700&family=Roboto:wght@400;500;700&display=swap">
<style>
  :root{
    --bg:#1f78ad;
    --brand:#1e84bd;
    --ink:#1b1b1b;
    --muted:#555;
    --line:#dfe3e6;
    --card:#ffffff;
    --alert:#e0201b;
    --placeholder-a:#f1f2f3;
    --placeholder-b:#dcdfe2;
  }
  *{box-sizing:border-box;margin:0;padding:0}
  html,body{width:1200px;height:1007px;overflow:hidden}
  body{background:var(--bg);font-family:'Roboto',sans-serif;color:var(--ink);position:relative}

  .screen{position:absolute;width:265px;height:576px;background:var(--card);border-radius:26px;overflow:hidden;box-shadow:0 14px 30px rgba(0,0,0,.25)}
  .screen--contents{left:134px;top:74px}
  .screen--about{left:483px;top:216px}
  .screen--pre{left:834px;top:323px}

  .app-header{position:absolute;top:34px;left:0;right:0;height:24px;display:flex;align-items:center;justify-content:space-between;padding:0 32px}
  .brand{display:flex;align-items:center;gap:5px;font-size:15px;font-weight:500;color:var(--ink);letter-spacing:-.2px}
  .brand-dot{width:20px;height:20px;border-radius:50%;background:var(--brand)}
  .icon-btn{width:16px;height:14px;display:block}

  .page-title{position:absolute;left:0;right:0;text-align:center;font-family:'Montserrat',sans-serif;font-weight:700;font-size:15.5px;letter-spacing:.2px;color:var(--ink)}
  .page-title span{color:var(--brand)}
  .title-rule{position:absolute;left:50%;width:36px;height:2px;margin-left:-18px;background:var(--brand)}

  .toc{position:absolute;left:33px;top:110px;width:198px;list-style:none}
  .toc-item{height:40px;margin-bottom:19px;background:#fff;border-radius:20px;box-shadow:0 2px 6px rgba(0,0,0,.14);display:flex;align-items:center;padding-left:6px;gap:14px}
  .toc-icon{flex:none;width:27px;height:27px;border-radius:50%;background:var(--brand);display:flex;align-items:center;justify-content:center;color:#fff;font-size:10px;font-weight:700}
  .toc-icon svg{width:12px;height:12px}
  .toc-title{font-size:10px;font-weight:500;line-height:1.3}
  .toc-sub{font-size:8.8px;color:var(--muted);line-height:1.3;white-space:nowrap}

  .faq{position:absolute;left:30px;top:161px;width:205px;list-style:none}
  .faq-item{height:33px;margin-bottom:10px;border:1px solid var(--line);display:flex;align-items:center;justify-content:space-between;padding:0 6px 0 5px;font-size:8.4px;color:#333;white-space:nowrap}
  .caret{flex:none;width:0;height:0;border-left:3px solid transparent;border-right:3px solid transparent;border-top:3.5px solid #333}

  .figure{position:absolute}
  .figure--anatomy{left:36px;top:348px;width:193px;height:152px;background:linear-gradient(160deg,var(--placeholder-a),var(--placeholder-b))}
  .figure--photo{left:34px;top:124px;width:200px;height:139px;background:linear-gradient(135deg,#eef1f5,#c7d3e2 50%,#f3f4f6)}

  .segmented{position:absolute;left:36px;top:280px;width:195px;display:flex;gap:5px}
  .segment{flex:1;height:19px;border:1px solid var(--brand);font-size:6.8px;font-weight:500;display:flex;align-items:center;justify-content:center;color:var(--brand);text-transform:uppercase}
  .segment--active{background:var(--brand);color:#fff}
  .task-hint{position:absolute;left:0;right:0;top:309px;display:flex;justify-content:center;align-items:center;gap:5px;font-size:9.2px;font-weight:500;color:var(--alert)}
  .task-hint svg{width:10px;height:10px}
  .tasks{position:absolute;left:36px;top:334px;width:195px;list-style:none}
  .task{height:23px;margin-bottom:5.4px;box-shadow:0 1px 4px rgba(0,0,0,.14);display:flex;align-items:center;padding:0 6px;font-size:7.8px;color:#333;gap:8px}
  .task-box{width:10px;height:10px;border:1px solid #ccc;flex:none}
  .task-label{flex:1}
  .task-toggle{width:14px;height:14px;background:#f1f1f1;display:flex;align-items:center;justify-content:center}

  .tab-bar{position:absolute;left:0;right:0;bottom:0;height:41px;background:var(--brand);display:flex}
  .tab{flex:1;display:flex;flex-direction:column;align-items:center;justify-content:center;gap:3px;color:#fff;font-size:7.4px;font-weight:500;border-right:1px solid rgba(255,255,255,.35)}
  .tab:last-child{border-right:none}
  .tab svg{width:10px;height:10px;fill:#fff}
  .tab--active{box-shadow:inset 0 -3px 0 #fff}
</style>
</head>
<body>

<svg width="0" height="0" style="position:absolute">
  <defs>
    <symbol id="i-back" viewBox="0 0 16 14"><path d="M1 7h15M6 2L1 7l5 5" stroke="#111" stroke-width="2" fill="none"/></symbol>
    <symbol id="i-menu" viewBox="0 0 16 14"><path d="M0 2h16M0 7h16M0 12h16" stroke="#111" stroke-width="2.2"/></symbol>
    <symbol id="i-home" viewBox="0 0 10 10"><path d="M5 0L0 5h1.5v5h2.5V7h2v3h2.5V5H10z"/></symbol>
    <symbol id="i-doc" viewBox="0 0 10 10"><path d="M1.5 0h5l2.5 2.5V10h-7.5zM3 5h4v1H3zm0 2h4v1H3z"/></symbol>
    <symbol id="i-user" viewBox="0 0 10 10"><circle cx="5" cy="3" r="2.5"/><path d="M0.5 10c0-3 2-4.5 4.5-4.5S9.5 7 9.5 10z"/></symbol>
    <symbol id="i-gear" viewBox="0 0 10 10"><circle cx="5" cy="5" r="3.6"/><path d="M4.2 0h1.6v2H4.2zM4.2 8h1.6v2H4.2zM0 4.2h2v1.6H0zM8 4.2h2v1.6H8z"/><circle cx="5" cy="5" r="1.5" fill="#1e84bd"/></symbol>
  </defs>
</svg>

<section class="screen screen--contents">
  <header class="app-header">
    <svg class="icon-btn"><use href="#i-back"/></svg>
    <div class="brand"><span class="brand-dot"></span>CAREPATH</div>
    <svg class="icon-btn"><use href="#i-menu"/></svg>
  </header>
  <h1 class="page-title" style="top:78px">TABLE OF <span>CONTENT</span></h1>
  <ul class="toc">
    <li class="toc-item"><span class="toc-icon"><svg viewBox="0 0 12 12"><path d="M3 1h7l-1 10H2z" fill="#fff"/></svg></span><div><div class="toc-title">About Procedure</div><div class="toc-sub">Why and How is it done</div></div></li>
    <li class="toc-item"><span class="toc-icon">123</span><div><div class="toc-title">Pre Procedure</div><div class="toc-sub">How to get ready</div></div></li>
    <li class="toc-item"><span class="toc-icon"><svg viewBox="0 0 12 12"><path d="M7 1a5 5 0 1 0 4 7A4 4 0 0 1 7 1z" fill="none" stroke="#fff" stroke-width="1.3"/></svg></span><div><div class="toc-title">Procedure</div><div class="toc-sub">The day of the procedure in the room</div></div></li>
    <li class="toc-item"><span class="toc-icon"><svg viewBox="0 0 12 12"><path d="M0 6c2-3 10-3 12 0-2 3-10 3-12 0z" fill="#fff"/><circle cx="6" cy="6" r="1.8" fill="#1e84bd"/></svg></span><div><div class="toc-title">Recovery</div><div class="toc-sub">Expectations immediately Surgery</div></div></li>
    <li class="toc-item"><span class="toc-icon"><svg viewBox="0 0 10 10" fill="#fff"><use href="#i-home"/></svg></span><div><div class="toc-title">At Home</div><div class="toc-sub">How to care for yourself afterwards</div></div></li>
    <li class="toc-item"><span class="toc-icon">?</span><div><div class="toc-title">What To Do If</div><div class="toc-sub">Responding to your issues</div></div></li>
    <li class="toc-item"><span class="toc-icon"><svg viewBox="0 0 12 12"><path d="M2 6l3 3 5-6" stroke="#fff" stroke-width="1.8" fill="none"/></svg></span><div><div class="toc-title">Success</div><div class="toc-sub">Feedback and who did this app</div></div></li>
  </ul>
  <nav class="tab-bar">
    <div class="tab"><svg><use href="#i-home"/></svg>Home</div>
    <div class="tab tab--active"><svg><use href="#i-doc"/></svg>Contents</div>
    <div class="tab"><svg><use href="#i-user"/></svg>Team</div>
    <div class="tab"><svg><use href="#i-gear"/></svg>Settings</div>
  </nav>
</section>

<section class="screen screen--about">
  <header class="app-header">
    <svg class="icon-btn"><use href="#i-back"/></svg>
    <div class="brand"><span class="brand-dot"></span>CAREPATH</div>
    <svg class="icon-btn"><use href="#i-menu"/></svg>
  </header>
  <h1 class="page-title" style="top:102px;font-size:17px">ABOUT <span>PROCEDURE</span></h1>
  <div class="title-rule" style="top:131px"></div>
  <ul class="faq">
    <li class="faq-item">Is it too late to prevent gallbladder disease ?<span class="caret"></span></li>
    <li class="faq-item">What will happen If idon't have thisprocedure ?<span class="caret"></span></li>
    <li class="faq-item">Are there alternative solutions ?<span class="caret"></span></li>
    <li class="faq-item">What are the risks of this procedure ?<span class="caret"></span></li>
  </ul>
  <div class="figure figure--anatomy" role="img" aria-label="Labelled medical illustration of the liver, gallbladder and common bile duct"></div>
  <nav class="tab-bar">
    <div class="tab"><svg><use href="#i-home"/></svg>Home</div>
    <div class="tab tab--active"><svg><use href="#i-doc"/></svg>Contents</div>
    <div class="tab"><svg><use href="#i-user"/></svg>Team</div>
    <div class="tab"><svg><use href="#i-gear"/></svg>Settings</div>
  </nav>
</section>

<section class="screen screen--pre">
  <header class="app-header">
    <svg class="icon-btn"><use href="#i-back"/></svg>
    <div class="brand"><span class="brand-dot"></span>CAREPATH</div>
    <svg class="icon-btn"><use href="#i-menu"/></svg>
  </header>
  <h1 class="page-title" style="top:87px;font-size:17px">PRE <span>PROCEDURE</span></h1>
  <div class="title-rule" style="top:117px"></div>
  <div class="figure figure--photo" role="img" aria-label="Photo of a patient holding her abdomen in discomfort"></div>
  <div class="segmented">
    <div class="segment segment--active">Weeks Before</div>
    <div class="segment">Day Before</div>
  </div>
  <div class="task-hint"><svg viewBox="0 0 10 10"><rect x=".6" y="1.6" width="7.8" height="7.8" fill="none" stroke="#e0201b" stroke-width="1.1"/><path d="M2.5 5l2 2L9.5 1" stroke="#e0201b" stroke-width="1.3" fill="none"/></svg>Check When TaskIsCompleted</div>
  <ul class="tasks">
    <li class="task"><span class="task-box"></span><span class="task-label">Pre-Operative Appointment</span><span class="task-toggle"><span class="caret"></span></span></li>
    <li class="task"><span class="task-box"></span><span class="task-label">8 Weeks Before</span><span class="task-toggle"><span class="caret"></span></span></li>
    <li class="task"><span class="task-box"></span><span class="task-label">6 Weeks Before</span><span class="task-toggle"><span class="caret"></span></span></li>
    <li class="task"><span class="task-box"></span><span class="task-label">2 Weeks Before</span><span class="task-toggle"><span class="caret"></span></span></li>
    <li class="task"><span class="task-box"></span><span class="task-label">1 Weeks Before</span><span class="task-toggle"><span class="caret"></span></span></li>
  </ul>
  <nav class="tab-bar">
    <div class="tab"><svg><use href="#i-home"/></svg>Home</div>
    <div class="tab tab--active"><svg><use href="#i-doc"/></svg>Contents</div>
    <div class="tab"><svg><use href="#i-user"/></svg>Team</div>
    <div class="tab"><svg><use href="#i-gear"/></svg>Settings</div>
  </nav>
</section>

</body>
</html>
```